Presentation and Communication Coaching Services Business needs updated interactive web site

I want to keep the color scheme, functionality, and pages of my current site, but with a newer/updated look. I need to improve security and simplify images, etc. (Please see current site http://brightwellvoicetutor.com ) This will need be functional on mobile devices, as well.

I'm attached to the scrolling client list and scrolling client feedback.

Industry/Entity Type

Professional Service

Font styles to use
Sans Serif

Colors
0356a4
f37122
33a6d7

Requirements
Must have
• scrolling client banner on home page, client comments slider, color scheme
• Please see current site: http://brightwellvoicetutor.com
Nice to have
• better action/appearance
Should not have
• I don't want it to look like all the other sites/templates

```html
<!DOCTYPE html>
<html lang="en">
<head>
<meta charset="utf-8">
<title>Brightwell Voice Tutoring – Home Page Concepts</title>
<link href="https://fonts.googleapis.com/css2?family=Poppins:ital,wght@0,400;0,500;0,600;0,700;1,400;1,600;1,800&display=swap" rel="stylesheet">
<style>
:root{
  --board:#efefef;
  --navy:#112b3c;
  --gold:#e8a623;
  --teal:#2f8fb2;
  --line:#3aa0c9;
  --white:#ffffff;
  --muted:#c9d3da;
  --ink:#1b1b1b;
  --play:#e3161b;
  --placeholder-warm:#8a6a45;
  --placeholder-soft:#5d5a52;
}
*{box-sizing:border-box;margin:0;padding:0}
html,body{width:1200px;height:2195px;overflow:hidden}
body{background:var(--board);font-family:"Poppins",Arial,sans-serif;color:var(--white);position:relative}

.mockup{position:absolute;top:85px;width:524px;background:var(--navy);box-shadow:0 1px 4px rgba(0,0,0,.15)}
.mockup--dark{left:57px}
.mockup--light{left:619px}

/* header */
.site-header{position:relative;height:61px;background:var(--navy)}
.mockup--light .site-header{background:var(--white)}
.top-tabs{position:absolute;left:284px;top:0;display:flex;height:14px;font-size:7px;font-weight:500}
.tab-phone{width:86px;background:var(--teal);clip-path:polygon(6% 0,100% 0,100% 100%,0 100%);text-align:center;line-height:14px}
.tab-login{width:80px;background:var(--gold);clip-path:polygon(0 0,100% 0,92% 100%,0 100%);text-align:center;line-height:14px}
.brand{position:absolute;left:40px;top:24px;font-size:17px;font-weight:400;letter-spacing:-.2px;color:var(--white)}
.mockup--light .brand{color:#2b2b2b}
.main-nav{position:absolute;left:258px;top:33px;display:flex;gap:11px;font-size:6.5px;font-weight:500;color:var(--white)}
.mockup--light .main-nav{color:#2b2b2b}

/* hero */
.hero{position:relative;height:271px}
.hero-photo{position:absolute;inset:0;background:linear-gradient(100deg,#a67a3e 0%,#b88842 40%,#7f7a40 70%,#7a5a2e 100%)}
.hero-copy{position:absolute;left:40px;top:80px}
.hero-title{font-size:17px;font-weight:700;line-height:22px;text-transform:uppercase}
.hero-sub{font-size:8px;margin-top:4px}
.btn{display:inline-block;border:1.4px solid var(--white);border-radius:12px;font-size:7px;font-weight:500;padding:4px 20px;margin-top:10px}
.btn--gold{border-color:var(--gold)}

.section-title{color:var(--gold);font-weight:800;font-style:italic;font-size:17px;text-transform:uppercase}

/* about */
.about{position:relative;height:278px;background:var(--navy)}
.about-portrait{position:absolute;left:45px;top:51px;width:190px;height:190px;border-radius:50%;background:linear-gradient(160deg,#7d7552,#5d5a4a)}
.about-ring{position:absolute;left:53px;top:59px;width:178px;height:178px;border-radius:50%;border:1.5px solid rgba(255,255,255,.85)}
.about-copy{position:absolute;left:294px;top:58px;width:195px}
.about-copy p{font-size:7px;line-height:13px;margin-top:10px}

/* services */
.services{position:relative;height:376px;background:linear-gradient(180deg,#131a20,#1c2327 40%,#161d22)}
.services .section-title{position:absolute;top:38px;width:100%;text-align:center;text-transform:none}
.service-card{position:absolute;width:181px;height:99px;border:1.6px solid var(--line);border-radius:4px;padding:20px 10px 0 52px}
.service-icon{position:absolute;left:-12px;top:-8px;width:48px;height:48px;border-radius:50%;border:1.6px solid var(--line);background:#1a2228;display:flex;align-items:center;justify-content:center}
.service-card h3{color:var(--gold);font-size:7px;font-weight:700;text-transform:uppercase}
.service-card p{font-size:6px;line-height:9.5px;margin-top:4px}
.sc1{left:72px;top:97px}.sc2{left:279px;top:97px}.sc3{left:72px;top:230px}.sc4{left:279px;top:230px}

/* video */
.video{position:relative;height:546px;background:var(--navy)}
.video .section-title{position:absolute;top:32px;width:100%;text-align:center}
.video-intro{position:absolute;top:68px;left:90px;width:344px;text-align:center;font-size:7px;line-height:13px}
.video-stage{position:absolute;left:0;right:0;top:180px;bottom:0;background:linear-gradient(180deg,#2e2a26,#1a1715 60%,#14110f)}
.video-thumb{position:absolute;left:105px;top:155px;width:313px;height:165px;background:linear-gradient(90deg,#7a5036,#a06a46 55%,#8a6040)}
.play{position:absolute;left:143px;top:69px;width:28px;height:28px;border-radius:50%;background:var(--play)}
.play::after{content:"";position:absolute;left:11px;top:8px;border-left:9px solid var(--white);border-top:6px solid transparent;border-bottom:6px solid transparent}
.pillars{position:absolute;top:392px;left:0;right:0}
.pillar{position:absolute;width:90px;margin-left:-45px;text-align:center}
.pillar-icon{width:40px;height:40px;border-radius:50%;border:1.5px solid var(--white);margin:0 auto;display:flex;align-items:center;justify-content:center}
.pillar h4{color:var(--gold);font-size:7.5px;font-weight:700;margin-top:9px}
.pillar p{font-size:6px;line-height:9px;margin-top:3px;font-weight:500}
.p1{left:155px}.p2{left:263px}.p3{left:367px}
.dots{position:absolute;display:flex;gap:4px;align-items:center;left:50%;transform:translateX(-50%)}
.dots i{width:4px;height:4px;border-radius:50%;background:var(--gold)}
.dots i.on{width:8px;height:8px;background:transparent;border:1.5px solid var(--gold);position:relative}
.dots i.on::after{content:"";position:absolute;inset:1.5px;border-radius:50%;background:var(--gold)}

/* reviews */
.reviews{position:relative;height:234px;background:var(--navy)}
.reviews .section-title{position:absolute;top:32px;width:100%;text-align:center}
.review{position:absolute;top:80px;width:215px}
.review-avatar{position:absolute;left:0;top:0;width:56px;height:56px;border-radius:50%;border:2px solid var(--white);background:var(--placeholder-soft)}
.review-mark{position:absolute;left:20px;top:58px;color:var(--gold);font-size:26px;font-weight:800;line-height:1}
.review-body{position:absolute;left:69px;top:0;width:140px}
.review-body q{font-size:6px;line-height:9.5px;font-style:italic;display:block}
.stars{color:var(--gold);font-size:11px;letter-spacing:1px;margin-top:4px}
.review-name{font-size:6.5px;font-weight:600;font-style:italic;margin-top:2px}
.r1{left:45px}.r2{left:272px}

/* partners */
.partners{position:relative;height:99px;background:linear-gradient(180deg,var(--white) 0 37px,var(--navy) 37px)}
.partners-card{position:absolute;left:75px;top:0;width:371px;height:99px;background:var(--white)}
.partners .section-title{position:absolute;top:10px;width:100%;text-align:center}
.arrows{position:absolute;left:336px;top:19px;display:flex;gap:4px}
.arrows span{width:11px;height:11px;border-radius:50%;background:var(--ink)}
.arrows span+span{background:var(--gold)}
.partner-badge{position:absolute;top:47px;width:83px;height:36px;background:var(--white);box-shadow:0 1px 4px rgba(0,0,0,.18)}
.b1{left:14px}.b2{left:141px}.b3{left:267px}

/* footer */
.site-footer{position:relative;height:158px;background:var(--navy);font-size:6.5px}
.fcol{position:absolute;top:29px}
.fcol h5{font-size:8px;font-weight:500;margin-bottom:6px}
.fcol li{list-style:none;line-height:9.5px}
.contact li{display:flex;gap:7px;align-items:flex-start;margin-bottom:5px;line-height:8px;white-space:nowrap}
.ico{flex:none;width:11px;height:11px;border-radius:50%;border:1px solid var(--white);display:flex;align-items:center;justify-content:center}
.social li{display:flex;gap:6px;align-items:center;margin-bottom:4px}
.fc1{left:40px;width:145px;font-size:6px}.fc2{left:192px}.fc3{left:284px}.fc4{left:382px;width:110px}
.fc4 p{line-height:8.5px}
.signup{display:flex;margin-top:8px;height:12px}
.signup span{flex:1;background:var(--white);color:#888;font-size:4.5px;padding-left:4px;line-height:12px}
.signup b{width:14px;background:var(--gold)}
.copyright{position:absolute;top:135px;width:100%;text-align:center;font-size:5px;color:var(--muted)}
</style>
</head>
<body>

<!-- concept A: dark header -->
<div class="mockup mockup--dark">
  <header class="site-header">
    <div class="top-tabs"><div class="tab-phone">646.555.0147</div><div class="tab-login">Client Login</div></div>
    <div class="brand">brightwellvoicetutor</div>
    <nav class="main-nav"><span>Home</span><span>About Us</span><span>Services</span><span>Reviews</span><span>Clients</span><span>Contact Us</span></nav>
  </header>
  <section class="hero">
    <div class="hero-photo" role="img" aria-label="Stage microphone in front of a warm, blurred audience"></div>
    <div class="hero-copy">
      <h1 class="hero-title">Welcome to Brightwell<br>Voice Tutoring</h1>
      <p class="hero-sub">You're good at what you do. Learn How to let it show.</p>
      <span class="btn">Read More</span>
    </div>
  </section>
  <section class="about">
    <div class="about-portrait" role="img" aria-label="Portrait of the coach"></div>
    <div class="about-ring"></div>
    <div class="about-copy">
      <h2 class="section-title">About Us</h2>
      <p>An individual works hard to reach a place of respect and authority in her or his chosen profession. Effective self-presentation adds confidence and allows one's unique personality and expertise to shine through – in fact, it is key in separating from the pack and reaching higher goals. As competition increases, these skills become more essential in demonstrating value to an employer, manager, or board.</p>
      <span class="btn btn--gold" style="margin-top:16px">Read More</span>
    </div>
  </section>
  <section class="services" role="img" aria-label="Dim conference room backdrop">
    <h2 class="section-title">Our Services</h2>
    <div class="service-card sc1"><div class="service-icon"><svg width="22" height="22" viewBox="0 0 22 22" fill="none" stroke="#e8a623" stroke-width="1.4"><rect x="8" y="3" width="11" height="8"/><circle cx="6" cy="9" r="2.5"/><path d="M2 20v-5a4 4 0 0 1 8 0v5"/></svg></div><h3>Coaching</h3><p>One-on-one coaching combining skills and techniques developed over years of training and professional experience in the performing arts as well as delivering successful</p></div>
    <div class="service-card sc2"><div class="service-icon"><svg width="22" height="22" viewBox="0 0 22 22" fill="none" stroke="#e8a623" stroke-width="1.4"><rect x="2" y="3" width="8" height="6"/><rect x="12" y="3" width="8" height="6"/><circle cx="6" cy="14" r="2"/><circle cx="16" cy="14" r="2"/><path d="M2 20a4 3 0 0 1 8 0M12 20a4 3 0 0 1 8 0"/></svg></div><h3>Accents</h3><p>Many speaking English as a second or third language have never been given direct, one-on-one feedback for challenging sounds and stress patterns that exist in English and nowhere else.</p></div>
    <div class="service-card sc3"><div class="service-icon"><svg width="22" height="22" viewBox="0 0 22 22" fill="none" stroke="#e8a623" stroke-width="1.4"><rect x="3" y="5" width="16" height="13" rx="2"/><path d="M3 9h16M7 3v4M15 3v4"/></svg></div><h3>Custom Workshops</h3><p>Miranda does not recycle on-the-shelf pre-made programs. She researches your company's culture, industry, differentiators, goals, and the experience level of the team.</p></div>
    <div class="service-card sc4"><div class="service-icon"><svg width="22" height="22" viewBox="0 0 22 22" fill="none" stroke="#e8a623" stroke-width="1.4"><rect x="3" y="3" width="16" height="11"/><circle cx="11" cy="8" r="2"/><path d="M7 20l4-6 4 6M8 13a3 3 0 0 1 6 0"/></svg></div><h3>Keynote Speeches</h3><p>Miranda elevates conferences and events to new levels of enthusiasm and engagement. Find out how she can shift mindset around presenting and communication and</p></div>
  </section>
  <section class="video">
    <h2 class="section-title">Video</h2>
    <p class="video-intro">Lorem Ipsum is simply dummy text of the printing and typesetting industry. Lorem Ipsum has been the industry's standard dummy text ever since the 1500s, when an unknown printer took a galley of type and scrambled it to make a type specimen book. It has survived not only five centuries, but also the leap into electronic typesetting, remaining essentially unchanged.</p>
    <div class="video-stage" role="img" aria-label="Audience seated in a darkened hall"></div>
    <div class="video-thumb" role="img" aria-label="Video still of the coach speaking to camera"><span class="play"></span></div>
    <div class="pillars">
      <div class="pillar p1"><div class="pillar-icon"><svg width="18" height="18" viewBox="0 0 18 18" fill="none" stroke="#fff" stroke-width="1.3"><path d="M5 2h8v5a4 4 0 0 1-8 0zM9 11v3M5 16h8M5 4H2a3 3 0 0 0 3 4M13 4h3a3 3 0 0 1-3 4"/></svg></div><h4>THE GOAL</h4><p>Deliver a focused, engaging message that leads to a successful outcome.</p></div>
      <div class="pillar p2"><div class="pillar-icon"><svg width="18" height="18" viewBox="0 0 18 18" fill="none" stroke="#fff" stroke-width="1.3"><rect x="2" y="6" width="11" height="9"/><path d="M5 3h11v9"/><path d="M6 9l3 2-3 2z"/></svg></div><h4>THE RESULT</h4><p>A natural, confident delivery that comes from knowing what you're doing.</p></div>
      <div class="pillar p3"><div class="pillar-icon"><svg width="18" height="18" viewBox="0 0 18 18" fill="none" stroke="#fff" stroke-width="1.3"><circle cx="5" cy="7" r="2"/><circle cx="13" cy="7" r="2"/><path d="M1 15a4 4 0 0 1 8 0M9 15a4 4 0 0 1 8 0M7 2h4v2H7z"/></svg></div><h4>THE SOLUTION</h4><p>Obtain individualized coaching to grow these necessary skills and establish</p></div>
    </div>
    <div class="dots" style="top:506px"><i></i><i class="on"></i><i></i></div>
  </section>
  <section class="reviews">
    <h2 class="section-title">Customers Reviews</h2>
    <div class="review r1"><div class="review-avatar" role="img" aria-label="Client portrait"></div><span class="review-mark">"</span><div class="review-body"><q>Miranda showed me how one word or phrase and a certain intonation can influence the outcome of a speech. After one session, I began to reap the rewards of her coaching and after a series of sessions</q><div class="stars">★★★★★</div><div class="review-name">CEO, Northgate - New York, NY</div></div></div>
    <div class="review r2"><div class="review-avatar" role="img" aria-label="Client portrait"></div><span class="review-mark">"</span><div class="review-body"><q>I've had the pleasure of working with Miranda, both on a one-on-one basis, as well as working with our group on oral presentations at Harborline Trust. She's a great resource and partner.</q><div class="stars">★★★★★</div><div class="review-name">Managing Director, Harborline Trust New York, NY</div></div></div>
    <div class="dots" style="top:204px"><i></i><i class="on"></i><i></i></div>
  </section>
  <section class="partners">
    <div class="partners-card">
      <h2 class="section-title">Our Partners</h2>
      <div class="arrows"><span></span><span></span></div>
      <div class="partner-badge b1"></div><div class="partner-badge b2"></div><div class="partner-badge b3"></div>
    </div>
  </section>
  <footer class="site-footer">
    <div class="fcol fc1"><h5>CONTACT US</h5><ul class="contact">
      <li><span class="ico"><svg width="6" height="7" viewBox="0 0 6 7"><path d="M3 7S.5 4 .5 2.6a2.5 2.5 0 0 1 5 0C5.5 4 3 7 3 7z" fill="#fff"/></svg></span><span>Address :<br>Riverton, NY 10990,<br>USA</span></li>
      <li><span class="ico"><svg width="6" height="6" viewBox="0 0 6 6"><path d="M1 .5l1.2 1.6-.6.8a3.5 3.5 0 0 0 1.5 1.5l.8-.6L5.5 5 4.8 5.6C2.5 5.4.6 3.5.4 1.2z" fill="#fff"/></svg></span><span>Call Us :<br>646.555.0147</span></li>
      <li><span class="ico"><svg width="6" height="5" viewBox="0 0 6 5" fill="none" stroke="#fff" stroke-width=".7"><rect x=".4" y=".4" width="5.2" height="4.2"/><path d="M.4.6L3 2.8 5.6.6"/></svg></span><span>E - Mail :<br>info@brightwellvoicetutor.com</span></li></ul></div>
    <div class="fcol fc2"><h5>Quick Links</h5><ul><li>Home</li><li>About Us</li><li>Services</li><li>Reviews</li><li>Clients</li><li>Contact Us</li></ul></div>
    <div class="fcol fc3"><h5>GET IN TOUCH</h5><ul class="social"><li><span class="ico"></span>Newsfeed</li><li><span class="ico"></span>Chirper</li><li><span class="ico"></span>ProLink</li><li><span class="ico"></span>Snapshots</li></ul></div>
    <div class="fcol fc4"><h5>Newsletter</h5><p>Lorem Ipsum has been the industry's standard dummy text ever since the 1500s.</p><div class="signup"><span>Enter your email address</span><b></b></div></div>
    <div class="copyright">© 2019 Copyrights | All Rights Reserved</div>
  </footer>
</div>

<!-- concept B: light header -->
<div class="mockup mockup--light">
  <header class="site-header">
    <div class="top-tabs"><div class="tab-phone">646.555.0147</div><div class="tab-login">Client Login</div></div>
    <div class="brand">brightwellvoicetutor</div>
    <nav class="main-nav"><span>Home</span><span>About Us</span><span>Services</span><span>Reviews</span><span>Clients</span><span>Contact Us</span></nav>
  </header>
  <section class="hero">
    <div class="hero-photo" role="img" aria-label="Stage microphone in front of a warm, blurred audience"></div>
    <div class="hero-copy">
      <h1 class="hero-title">Welcome to Brightwell<br>Voice Tutoring</h1>
      <p class="hero-sub">You're good at what you do. Learn How to let it show.</p>
      <span class="btn">Read More</span>
    </div>
  </section>
  <section class="about">
    <div class="about-portrait" role="img" aria-label="Portrait of the coach"></div>
    <div class="about-ring"></div>
    <div class="about-copy">
      <h2 class="section-title">About Us</h2>
      <p>An individual works hard to reach a place of respect and authority in her or his chosen profession. Effective self-presentation adds confidence and allows one's unique personality and expertise to shine through – in fact, it is key in separating from the pack and reaching higher goals. As competition increases, these skills become more essential in demonstrating value to an employer, manager, or board.</p>
      <span class="btn btn--gold" style="margin-top:16px">Read More</span>
    </div>
  </section>
  <section class="services" role="img" aria-label="Dim conference room backdrop">
    <h2 class="section-title">Our Services</h2>
    <div class="service-card sc1"><div class="service-icon"><svg width="22" height="22" viewBox="0 0 22 22" fill="none" stroke="#e8a623" stroke-width="1.4"><rect x="8" y="3" width="11" height="8"/><circle cx="6" cy="9" r="2.5"/><path d="M2 20v-5a4 4 0 0 1 8 0v5"/></svg></div><h3>Coaching</h3><p>One-on-one coaching combining skills and techniques developed over years of training and professional experience in the performing arts as well as delivering successful</p></div>
    <div class="service-card sc2"><div class="service-icon"><svg width="22" height="22" viewBox="0 0 22 22" fill="none" stroke="#e8a623" stroke-width="1.4"><rect x="2" y="3" width="8" height="6"/><rect x="12" y="3" width="8" height="6"/><circle cx="6" cy="14" r="2"/><circle cx="16" cy="14" r="2"/><path d="M2 20a4 3 0 0 1 8 0M12 20a4 3 0 0 1 8 0"/></svg></div><h3>Accents</h3><p>Many speaking English as a second or third language have never been given direct, one-on-one feedback for challenging sounds and stress patterns that exist in English and nowhere else.</p></div>
    <div class="service-card sc3"><div class="service-icon"><svg width="22" height="22" viewBox="0 0 22 22" fill="none" stroke="#e8a623" stroke-width="1.4"><rect x="3" y="5" width="16" height="13" rx="2"/><path d="M3 9h16M7 3v4M15 3v4"/></svg></div><h3>Custom Workshops</h3><p>Miranda does not recycle on-the-shelf pre-made programs. She researches your company's culture, industry, differentiators, goals, and the experience level of the team.</p></div>
    <div class="service-card sc4"><div class="service-icon"><svg width="22" height="22" viewBox="0 0 22 22" fill="none" stroke="#e8a623" stroke-width="1.4"><rect x="3" y="3" width="16" height="11"/><circle cx="11" cy="8" r="2"/><path d="M7 20l4-6 4 6M8 13a3 3 0 0 1 6 0"/></svg></div><h3>Keynote Speeches</h3><p>Miranda elevates conferences and events to new levels of enthusiasm and engagement. Find out how she can shift mindset around presenting and communication and</p></div>
  </section>
  <section class="video">
    <h2 class="section-title">Video</h2>
    <p class="video-intro">Lorem Ipsum is simply dummy text of the printing and typesetting industry. Lorem Ipsum has been the industry's standard dummy text ever since the 1500s, when an unknown printer took a galley of type and scrambled it to make a type specimen book. It has survived not only five centuries, but also the leap into electronic typesetting, remaining essentially unchanged.</p>
    <div class="video-stage" role="img" aria-label="Audience seated in a darkened hall"></div>
    <div class="video-thumb" role="img" aria-label="Video still of the coach speaking to camera"><span class="play"></span></div>
    <div class="pillars">
      <div class="pillar p1"><div class="pillar-icon"><svg width="18" height="18" viewBox="0 0 18 18" fill="none" stroke="#fff" stroke-width="1.3"><path d="M5 2h8v5a4 4 0 0 1-8 0zM9 11v3M5 16h8M5 4H2a3 3 0 0 0 3 4M13 4h3a3 3 0 0 1-3 4"/></svg></div><h4>THE GOAL</h4><p>Deliver a focused, engaging message that leads to a successful outcome.</p></div>
      <div class="pillar p2"><div class="pillar-icon"><svg width="18" height="18" viewBox="0 0 18 18" fill="none" stroke="#fff" stroke-width="1.3"><rect x="2" y="6" width="11" height="9"/><path d="M5 3h11v9"/><path d="M6 9l3 2-3 2z"/></svg></div><h4>THE RESULT</h4><p>A natural, confident delivery that comes from knowing what you're doing.</p></div>
      <div class="pillar p3"><div class="pillar-icon"><svg width="18" height="18" viewBox="0 0 18 18" fill="none" stroke="#fff" stroke-width="1.3"><circle cx="5" cy="7" r="2"/><circle cx="13" cy="7" r="2"/><path d="M1 15a4 4 0 0 1 8 0M9 15a4 4 0 0 1 8 0M7 2h4v2H7z"/></svg></div><h4>THE SOLUTION</h4><p>Obtain individualized coaching to grow these necessary skills and establish</p></div>
    </div>
    <div class="dots" style="top:506px"><i></i><i class="on"></i><i></i></div>
  </section>
  <section class="reviews">
    <h2 class="section-title">Customers Reviews</h2>
    <div class="review r1"><div class="review-avatar" role="img" aria-label="Client portrait"></div><span class="review-mark">"</span><div class="review-body"><q>Miranda showed me how one word or phrase and a certain intonation can influence the outcome of a speech. After one session, I began to reap the rewards of her coaching and after a series of sessions</q><div class="stars">★★★★★</div><div class="review-name">CEO, Northgate - New York, NY</div></div></div>
    <div class="review r2"><div class="review-avatar" role="img" aria-label="Client portrait"></div><span class="review-mark">"</span><div class="review-body"><q>I've had the pleasure of working with Miranda, both on a one-on-one basis, as well as working with our group on oral presentations at Harborline Trust. She's a great resource and partner.</q><div class="stars">★★★★★</div><div class="review-name">Managing Director, Harborline Trust New York, NY</div></div></div>
    <div class="dots" style="top:204px"><i></i><i class="on"></i><i></i></div>
  </section>
  <section class="partners">
    <div class="partners-card">
      <h2 class="section-title">Our Partners</h2>
      <div class="arrows"><span></span><span></span></div>
      <div class="partner-badge b1"></div><div class="partner-badge b2"></div><div class="partner-badge b3"></div>
    </div>
  </section>
  <footer class="site-footer">
    <div class="fcol fc1"><h5>CONTACT US</h5><ul class="contact">
      <li><span class="ico"><svg width="6" height="7" viewBox="0 0 6 7"><path d="M3 7S.5 4 .5 2.6a2.5 2.5 0 0 1 5 0C5.5 4 3 7 3 7z" fill="#fff"/></svg></span><span>Address :<br>Riverton, NY 10990,<br>USA</span></li>
      <li><span class="ico"><svg width="6" height="6" viewBox="0 0 6 6"><path d="M1 .5l1.2 1.6-.6.8a3.5 3.5 0 0 0 1.5 1.5l.8-.6L5.5 5 4.8 5.6C2.5 5.4.6 3.5.4 1.2z" fill="#fff"/></svg></span><span>Call Us :<br>646.555.0147</span></li>
      <li><span class="ico"><svg width="6" height="5" viewBox="0 0 6 5" fill="none" stroke="#fff" stroke-width=".7"><rect x=".4" y=".4" width="5.2" height="4.2"/><path d="M.4.6L3 2.8 5.6.6"/></svg></span><span>E - Mail :<br>info@brightwellvoicetutor.com</span></li></ul></div>
    <div class="fcol fc2"><h5>Quick Links</h5><ul><li>Home</li><li>About Us</li><li>Services</li><li>Reviews</li><li>Clients</li><li>Contact Us</li></ul></div>
    <div class="fcol fc3"><h5>GET IN TOUCH</h5><ul class="social"><li><span class="ico"></span>Newsfeed</li><li><span class="ico"></span>Chirper</li><li><span class="ico"></span>ProLink</li><li><span class="ico"></span>Snapshots</li></ul></div>
    <div class="fcol fc4"><h5>Newsletter</h5><p>Lorem Ipsum has been the industry's standard dummy text ever since the 1500s.</p><div class="signup"><span>Enter your email address</span><b></b></div></div>
    <div class="copyright">© 2019 Copyrights | All Rights Reserved</div>
  </footer>
</div>

</body>
</html>
```